Chartered Professional Accounting Firm Needs a Business Card Design

We need a card design for an accounting firm based in Toronto, Ontario. The firm name is Pavel Ostrom Professional Corporation. The owner of the firm is a chartered professional accountant and a certified general accountant. Services of the firm include 60% tax preparation and consulting and 40% financial statements for corporation year-end. We would like a modern design. The color could be black, white, gray, blue or other color to bring more confidence to clients. The logo of the firm should be included in the design. Thanks

Name: Pavel Ostrom, CPA, CGA Address: 47 Maple Crest Rd. Richmond Hill, ON L7K 3B5 Telephone: (416) 562-3907 Fax:(416) 734-2165 Email: pavel@pavelostrom-example.ca

Accounting

```html
<!DOCTYPE html>
<html lang="en">
<head>
<meta charset="utf-8">
<title>Pavel Ostrom Professional Corporation – Business Card</title>
<link href="https://fonts.googleapis.com/css2?family=Cinzel:wght@400;700&family=Source+Sans+3:wght@400&display=swap" rel="stylesheet">
<style>
  :root {
    --backdrop: #e4e4e6;
    --navy: #2c2f86;
    --navy-deep: #1f2270;
    --navy-light: #4a4fb0;
    --paper: #ffffff;
    --grey: #9a9a9e;
    --ink: #3a3a3e;
    --rule: #b5b5b8;
  }
  * { margin: 0; padding: 0; box-sizing: border-box; }
  html, body { width: 1200px; height: 871px; overflow: hidden; background: var(--backdrop); }
  .sheet {
    width: 1200px; height: 871px;
    display: flex; align-items: center; justify-content: center; gap: 40px;
  }
  .card {
    position: relative; width: 540px; height: 309px; overflow: hidden;
    box-shadow: 0 6px 18px rgba(0,0,0,.22);
  }

  /* Front */
  .card-front {
    background: linear-gradient(135deg, var(--navy-light) 0%, var(--navy) 45%, var(--navy-deep) 100%);
  }
  .front-decor {
    position: absolute; right: 40px; top: 30px; width: 190px; height: 190px;
    border: 10px solid rgba(255,255,255,.08); background: rgba(255,255,255,.04);
  }
  .front-brand {
    position: absolute; left: 44px; bottom: 52px;
    display: flex; align-items: center; gap: 12px; color: #fff;
  }
  .brand-dot { width: 46px; height: 46px; border-radius: 50%; border: 3px solid currentColor; flex: none; }
  .brand-name { font-family: "Cinzel", serif; font-weight: 700; font-size: 26px; line-height: 1; letter-spacing: .5px; }
  .brand-sub { font-family: "Cinzel", serif; font-weight: 700; font-size: 10.5px; letter-spacing: .4px; margin-top: 3px; }
  .brand-role { font-family: "Cinzel", serif; font-weight: 400; font-size: 8.5px; letter-spacing: 1px; line-height: 1.25; }

  /* Back */
  .card-back { background: var(--paper); }
  .back-brand {
    position: absolute; left: 34px; top: 22px;
    display: flex; align-items: center; gap: 8px; color: var(--navy);
  }
  .back-brand .brand-dot { width: 34px; height: 34px; border-width: 2px; }
  .back-brand .brand-name { font-size: 20px; }
  .back-brand .brand-sub { font-size: 8px; margin-top: 2px; }
  .back-brand .brand-role { font-size: 6.5px; color: var(--grey); }
  .address {
    position: absolute; left: 40px; top: 98px;
    font-family: "Source Sans 3", sans-serif; font-size: 11.5px; letter-spacing: 1.4px; color: var(--ink); line-height: 1.75;
  }
  .divider { position: absolute; left: 40px; right: 40px; top: 140px; height: 1px; background: var(--rule); }
  .person {
    position: absolute; right: 40px; top: 118px;
    font-family: "Cinzel", serif; font-size: 16px; letter-spacing: 3px; color: var(--navy);
  }
  .contacts {
    position: absolute; left: 40px; top: 154px; list-style: none;
    font-family: "Source Sans 3", sans-serif; font-size: 11.5px; letter-spacing: 1.4px; color: var(--ink);
  }
  .contacts li { display: flex; align-items: center; gap: 12px; height: 22px; }
  .contacts svg { width: 13px; height: 13px; fill: var(--navy); flex: none; }
  .wave { position: absolute; left: 0; bottom: 0; width: 540px; height: 110px; }
</style>
</head>
<body>
<main class="sheet">

  <section class="card card-front" aria-label="Card front">
    <div class="front-decor"></div>
    <div class="front-brand">
      <span class="brand-dot"></span>
      <div>
        <div class="brand-name">PAVEL OSTROM</div>
        <div class="brand-sub">PROFESSIONAL CORPORATION</div>
        <div class="brand-role">CHARTERED PROFESSIONAL ACCOUNTANT<br>CERTIFIED GENERAL ACCOUNTANT</div>
      </div>
    </div>
  </section>

  <section class="card card-back" aria-label="Card back">
    <div class="back-brand">
      <span class="brand-dot"></span>
      <div>
        <div class="brand-name">PAVEL OSTROM</div>
        <div class="brand-sub">PROFESSIONAL CORPORATION</div>
        <div class="brand-role">CHARTERED PROFESSIONAL ACCOUNTANT<br>CERTIFIED GENERAL ACCOUNTANT</div>
      </div>
    </div>

    <address class="address" style="font-style:normal">47 Maple Crest Rd.<br>Richmond Hill, ON L7K 3B5</address>
    <div class="divider"></div>
    <div class="person">PAVEL OSTROM, CPA, CGA</div>

    <ul class="contacts">
      <li>
        <svg viewBox="0 0 16 16" aria-hidden="true"><path d="M3 1h3l1.5 4-2 1.2a9 9 0 0 0 4.3 4.3L11 8.5l4 1.5v3a2 2 0 0 1-2 2A12 12 0 0 1 1 3a2 2 0 0 1 2-2z"/></svg>
        (416) 562-3907
      </li>
      <li>
        <svg viewBox="0 0 16 16" aria-hidden="true"><path d="M4 1h8v4H4zM1 6h14v7h-3v2H4v-2H1zM5 10v4h6v-4z"/></svg>
        (416) 734-2165
      </li>
      <li>
        <svg viewBox="0 0 16 16" aria-hidden="true"><path d="M1 3h14v10H1zm1.5 1.2V12h11V4.2L8 8.5z"/></svg>
        pavel@pavelostrom-example.ca
      </li>
    </ul>

    <svg class="wave" viewBox="0 0 540 110" preserveAspectRatio="none" aria-hidden="true">
      <path d="M0 30 C120 10 250 70 540 90 L540 110 L0 110 Z" fill="var(--grey)"/>
      <path d="M0 40 C130 22 260 82 540 100 L540 110 L0 110 Z" fill="var(--paper)"/>
      <path d="M0 46 C140 30 270 88 540 104 L540 110 L0 110 Z" fill="var(--navy)"/>
    </svg>
  </section>

</main>
</body>
</html>
```